Tobias Ränkel and Co stationary design

Name of business:
Tobias Ränkel and Co

Can be written as:
Tobias Ränkel and Co
Tobias Ränkel & Co
tobias ränkel & co

If broken into letters:
TR&Co
tr&co

We are a Railway Safety Training Company
Our focus is on rail safety, Rail Management, Safety Management, Train Control Training, Accident Investigation.

.

Project Deadline Extended Reason: The original date was set to commence as soon as the logo contest finished. Sketch harbor started the project as soon as it was paid. Added Thursday, May 12, 2016

Target Market(s)

Professionals, CEO's and Managing Directors

Industry/Entity Type

Management Consulting

Font styles to use
Sans Serif

Requirements
Must have
• Professional, Sharp, Creative and modern
• Please note that this is for stationary concept which must include
• - business card
• - letterhead
• - envelope
• - with compliments slip
• - document cover (like book or folder cover)
• - dividers for folders....
• These must all have a common theme or style
Nice to have
• Keep if fresh
Should not have
• Please don't sent just fonts.... Must be creative

```html
<!DOCTYPE html>
<html lang="en">
<head>
<meta charset="utf-8">
<title>Tobias Ränkel &amp; Co – Business Card</title>
<link href="https://fonts.googleapis.com/css2?family=Open+Sans:wght@400;600;700&display=swap" rel="stylesheet">
<style>
  :root {
    --navy: #1e2f6b;
    --navy-deep: #172556;
    --red: #d2233c;
    --white: #ffffff;
    --paper: #f4f4f2;
    --stage: #e6e3dd;
  }
  * { margin: 0; padding: 0; box-sizing: border-box; }
  html, body {
    width: 1200px; height: 843px; overflow: hidden;
    background: var(--stage);
    font-family: "Open Sans", Arial, sans-serif;
  }
  .canvas { position: relative; width: 1200px; height: 843px; }

  .card {
    position: absolute; width: 600px; height: 343px;
    overflow: hidden; border-radius: 2px;
    box-shadow: 0 6px 18px rgba(0,0,0,0.18);
  }

  /* Back side */
  .card-back {
    left: 70px; top: 60px;
    background: linear-gradient(135deg, var(--navy) 0%, var(--navy-deep) 100%);
    color: var(--white);
  }
  .back-brand {
    position: absolute; left: 0; right: 0; top: 130px;
    display: flex; align-items: center; justify-content: center; gap: 16px;
  }
  .back-brand .brand-dot {
    width: 38px; height: 38px; border-radius: 50%; background: var(--white);
  }
  .back-brand .brand-name {
    font-weight: 700; font-size: 34px; letter-spacing: 0.2px; color: var(--white);
  }
  .back-web {
    position: absolute; left: 0; right: 0; bottom: 34px;
    text-align: center; font-size: 14px; letter-spacing: 6px; color: var(--white);
  }

  /* Front side */
  .card-front {
    left: 530px; top: 440px;
    background: linear-gradient(180deg, var(--white) 0%, var(--paper) 100%);
  }
  .front-shape { position: absolute; inset: 0; }
  .front-brand {
    position: absolute; left: 40px; top: 148px;
    display: flex; align-items: center; gap: 10px;
  }
  .front-brand .brand-dot {
    width: 22px; height: 22px; border-radius: 50%; background: var(--red);
  }
  .front-brand .brand-name {
    font-weight: 700; font-size: 23px; color: var(--navy);
  }
  .contact {
    position: absolute; right: 26px; top: 62px;
    text-align: right; color: var(--white);
    font-size: 14px; line-height: 18px;
  }
  .contact .person-name { font-weight: 700; font-size: 19px; letter-spacing: 0.5px; line-height: 22px; }
  .contact .person-title { font-size: 14px; letter-spacing: 0.5px; margin-bottom: 4px; }
  .contact .address { margin-bottom: 6px; }
  .contact .line { display: flex; justify-content: flex-end; align-items: center; gap: 8px; }
  .contact .icon { width: 13px; height: 13px; flex: none; }
</style>
</head>
<body>
<main class="canvas">

  <section class="card card-back" aria-label="Business card back">
    <div class="back-brand">
      <span class="brand-dot"></span>
      <span class="brand-name">Tobias Ränkel &amp; Co</span>
    </div>
    <p class="back-web">www.trcorail.com</p>
  </section>

  <section class="card card-front" aria-label="Business card front">
    <svg class="front-shape" width="600" height="343" viewBox="0 0 600 343">
      <circle cx="650" cy="205" r="318" fill="none" stroke="var(--red)" stroke-width="5"/>
      <circle cx="650" cy="205" r="308" fill="var(--navy)"/>
    </svg>

    <div class="front-brand">
      <span class="brand-dot"></span>
      <span class="brand-name">Tobias Ränkel &amp; Co</span>
    </div>

    <div class="contact">
      <p class="person-name">LENA HARTWIG</p>
      <p class="person-title">CEO/FOUNDER</p>
      <p class="address">4120 Juniper Row<br>Fairbanks, Alaska 99701</p>
      <p class="line">907 412 5583
        <svg class="icon" viewBox="0 0 16 16"><path fill="#fff" d="M3 1l3 3-1.5 2a9 9 0 0 0 5.5 5.5L12 10l3 3-2 2C7 15 1 9 1 3z"/></svg>
      </p>
      <p class="line">907 388 1460
        <svg class="icon" viewBox="0 0 16 16"><rect x="4" y="1" width="8" height="14" rx="1.5" fill="none" stroke="#fff" stroke-width="1.6"/><circle cx="8" cy="12.5" r="0.9" fill="#fff"/></svg>
      </p>
      <p class="line">907 219 7732
        <svg class="icon" viewBox="0 0 16 16"><rect x="4" y="1" width="8" height="5" fill="#fff"/><rect x="1" y="6" width="14" height="6" rx="1" fill="#fff"/><rect x="4" y="11" width="8" height="4" fill="#fff" stroke="var(--navy)" stroke-width="1"/></svg>
      </p>
      <p class="line">lena@trcorail.com
        <svg class="icon" viewBox="0 0 16 16"><rect x="1" y="3" width="14" height="10" fill="#fff"/><path d="M1 3l7 6 7-6" fill="none" stroke="var(--navy)" stroke-width="1.3"/></svg>
      </p>
      <p class="line">www.trcorail.com
        <svg class="icon" viewBox="0 0 16 16"><circle cx="8" cy="8" r="6.5" fill="none" stroke="#fff" stroke-width="1.5"/><ellipse cx="8" cy="8" rx="2.8" ry="6.5" fill="none" stroke="#fff" stroke-width="1.2"/><path d="M1.5 8h13" stroke="#fff" stroke-width="1.2"/></svg>
      </p>
    </div>
  </section>

</main>
</body>
</html>
```